Coaching landingpage/salespage need a layout

Hi!
We are two people from Sweden looking for help to design our coaching landingpage/salespage.

What about:
We need a nice modern timeless appealing Photoshop layout (landingpage) for our coaching page where we coach people to “how to get a richer lifestyle”.

Style of page:
We want the site to reflect seriousness but still harmonic. We would like somewhat colorful and (but not too crazy). After all, we are coaching about investments and private economy.
Responsive layout – consider stacking order when scaling down window width. Fullpage-design where content areas are 960 grid/max-width.

----------------------------------------------------------------------------
Content on page:
*Headersection – Logo and header image with the two coaches together and space for later on adding a video.

*On the landingpage the customers can read up on what we mean by a richer lifestyle (use dummy text). We show our Vardagskompassen (= Lifestyle matrix) and a little description about that. If the customers want to know more, they can click "read more (or a symbolic icon that relates to read more)" to expand a hidden div (section) where they can read more about Vardagskompassen. They can also minimize the section.

*3-4 Unique selling points “Four reasons why choose coaching” with nice designed number-icons and some place for text.

*The customer should also be able to read something about what happens during a typical coaching session, some bullets that summarize it (use dummy text) and a couple of headlines, maybe 3 or 4 (about what they need to prepare for themselves .eg Skype, headset/microphone etc).

*Offer/product section: A section where the customer can see what services we provide, choose product and click order. When customer click order they will arrive to an order-page (this one you don’t have to design) .
Our products are as followed: Bronze (single coaching session), Silver (small-package), Gold (large-package). Use provided graphics for these products.

*Testimonials section. Currently we have 2 good testimonials, but only with text no portrait picture.

Testimonial1: “Uppiggande och inspirerande! Kommer med enkla vardagstips såväl som svårare tips. Ett roligt sätt att få en spark i baken, så att ekonomi-energin bibehålls! Tack för ett bra samtal!" - Helena Brattvik

Testimonial2: "Värdefullast för mig var kunskapen om alternativa investeringssställen som inte är börs eller eget ägande." - Annika Sjöstedt

*Section with portraits and info about the coaches (currently 2 coaches, but in future will be several, so a design-section that’s lets us add more coaches).

*Footer-section
------------------------------------------------------------------------

Colors:
Use Vardagskompassen (attached file) as colorinspiration. Doesn’t have to be exactly those colors, you can use similar colors if it is more pleasing to the eye and you can also use complementary colors.

Currently we have tried of our own but don't really nail it with any apealing design. This is what we have done so far but we want to replace it with your more professional design:

https://www.harborkite.se/full/Page/coaching13
-------------------------------------------------------------

SUMMARIZE of the above design-description:

* Our logo (attached psd-file with smart-object. You can try different colors with color-overlay)

*Apealing headerimage with portrait (attached file "big_portrait")

*Introduction text (use dummy text about 100 words)

*Text about Vardagskompassen (use dummy text about 200 words)

*Vardagskompassen (attached psd-file with smart-object)

*What we are covering during a coaching session (dummy text about 200 words and about 5 or 6 bullets)

*3-4 Unique Selling Points with stylish number icons (not 2 small) and some text.
*Our offers Bronze, Silver, Gold (attached pictures)
*Testimonials
*Picture & info about coaches (attached pictures, choose whichever suits you)
*Footer

Please comment if there are questions.

Target Market(s)

People who want to learn how to create a richer lifestyle which involves more freedom and a better well-being

Number of Pages Required

1 page

Font styles to use
Sans Serif
Other font styles liked:
• Roboto

Requirements
Should not have
• A cheezy unmodern landingpage with lots of texts and 10 sign-up buttons.
• This page is not a site about capturing emails and building lists by provide a "best-guide-for-something". It´s about getting people to book and pay for one or more coaching-sessions.

```html
<!DOCTYPE html>
<html lang="sv">
<head>
<meta charset="utf-8">
<title>Harbor Kite – Coaching</title>
<link href="https://fonts.googleapis.com/css2?family=Lato:ital,wght@0,400;0,700;0,900;1,400&family=Raleway:wght@300;400&display=swap" rel="stylesheet">
<style>
:root{
  --navy:#2f5a80;
  --navy-dark:#244a6b;
  --navy-light:#3b6a94;
  --accent:#3a76a6;
  --ink:#222;
  --text:#444;
  --muted:#777;
  --soft:#f0f0f0;
  --line:#d6d6d6;
  --footer:#333435;
  --footer-bottom:#232425;
  --white:#fff;
}
*{margin:0;padding:0;box-sizing:border-box}
html,body{width:1200px;height:3516px;overflow:hidden}
body{position:relative;font-family:'Lato',sans-serif;color:var(--text);background:var(--white)}
section,header,footer{position:absolute;left:0;width:1200px}
.abs{position:absolute}

/* header */
.topbar{top:0;height:117px;background:linear-gradient(#3a6893,var(--navy));border-top:4px solid #1f4566}
.brand{left:176px;top:34px;display:flex;align-items:center;gap:16px;color:var(--white);font-family:'Raleway',sans-serif;font-weight:300;font-size:30px;letter-spacing:5px}
.brand-mark{width:46px;height:46px;border:2px solid var(--white);border-radius:4px}
.phone{left:872px;top:44px;display:flex;align-items:center;gap:12px;color:var(--white);font-size:22px}

/* hero */
.hero{top:117px;height:488px;background:linear-gradient(100deg,#2b2a26 0%,#6a5a3e 30%,#b49667 55%,#6e5a3b 80%,#3a3226 100%)}
.hero-title{left:176px;top:290px;color:var(--white);font-family:'Raleway',sans-serif;font-size:37px;line-height:46px;text-transform:uppercase;font-weight:300}
.btn-start{left:173px;top:399px;width:232px;height:51px;background:var(--navy);border:2px solid #cfd9e3;border-radius:4px;color:var(--white);font-weight:700;font-size:23px;display:flex;align-items:center;justify-content:center;letter-spacing:.5px}
.video{left:544px;top:75px;width:464px;height:375px;background:linear-gradient(#eceae6,#cfcbc4);}
.video-stage{position:absolute;inset:0 0 47px 0;background:linear-gradient(135deg,#f3f2ef,#bdb6aa 70%,#4a4a4a)}
.video-play{position:absolute;left:202px;top:147px;width:62px;height:62px;border-radius:50%;background:rgba(255,255,255,.75)}
.video-bar{position:absolute;left:0;bottom:0;width:464px;height:47px;background:linear-gradient(#3e4a55,#1d252c)}

/* section headings */
.sec-title{left:0;width:1200px;text-align:center;font-weight:900;font-size:36px;color:var(--ink);text-transform:uppercase;letter-spacing:.5px}
.sec-title span{color:var(--accent);font-weight:700}
.divider{left:310px;width:580px;height:14px}
.divider::before{content:"";position:absolute;left:0;right:0;top:6px;height:2px;background:linear-gradient(90deg,transparent,#c9c9c9 20%,#c9c9c9 80%,transparent)}
.divider::after{content:"";position:absolute;left:281px;top:0;width:18px;height:14px;background:#333;box-shadow:0 0 0 6px var(--bg,#fff)}
.lede{left:192px;width:816px;text-align:center;font-size:14px;line-height:22px;color:var(--text)}
.btn-small{height:37px;background:var(--navy);color:var(--white);font-weight:700;font-size:15px;display:flex;align-items:center;justify-content:center;border-radius:2px}

.about{top:605px;height:340px;background:var(--soft);--bg:var(--soft)}
.why{top:945px;height:428px;background:var(--white)}
.portrait{left:511px;top:222px;width:218px;height:206px;background:linear-gradient(#d9cfc4,#4b4d55 70%,#1d2026)}

/* lifestyles */
.life{top:1373px;height:378px;background:var(--navy)}
.life-pointer{left:565px;top:1751px;width:70px;height:35px}
.life-item{width:300px;color:var(--white)}
.life-item h3{font-size:21px;font-weight:900;text-transform:uppercase;margin-bottom:8px}
.life-item p{font-size:14px;line-height:20px}
.life-item.left{text-align:right}
.life-icon{width:46px;height:46px;border-radius:50%}
.life-lines{left:440px;top:60px;width:320px;height:260px}

/* products */
.products{top:1786px;height:616px;background:var(--white)}
.product{width:260px;text-align:center}
.product h3{font-size:27px;font-weight:700;color:var(--navy)}
.medal{width:116px;height:116px;border-radius:50%;margin:26px auto 30px}
.price{font-size:34px;font-weight:900;color:var(--ink)}
.includes{font-size:21px;color:var(--ink);margin-top:16px}
.product .btn-small{width:146px;height:47px;font-size:24px;font-weight:400;margin:24px auto 0}
.col-rule{width:1px;background:var(--line)}

/* testimonials */
.testimonials{top:2402px;height:387px;background:#eeeeee;--bg:#eeeeee}
.quote{width:422px}
.quote p{font-style:italic;font-size:15px;line-height:25px;color:#444;padding-left:64px;padding-right:40px;position:relative}
.quote p::before{content:"\201C";position:absolute;left:20px;top:-18px;font-size:64px;color:#b5b5b5;font-style:normal;font-family:Georgia,serif}
.quote-rule{position:absolute;left:0;width:422px;height:2px;background:linear-gradient(90deg,transparent,#bdbdbd 30%,#bdbdbd 70%,transparent)}
.quote cite{position:absolute;right:80px;font-style:normal;font-weight:700;font-size:14px;color:var(--navy)}
.arrow{width:20px;height:40px}

/* team */
.team{top:2789px;height:427px;background:var(--white)}
.coach{width:414px;height:218px;background:#fafafa;border:1px solid #e5e5e5;border-radius:4px;box-shadow:0 2px 4px rgba(0,0,0,.08)}
.coach-photo{position:absolute;left:8px;top:-24px;width:94px;height:94px;border-radius:50%;border:4px solid var(--white);box-shadow:0 0 0 1px #ccc}
.coach-photo.a{background:linear-gradient(#7a6b5a,#2f2b28)}
.coach-photo.b{background:linear-gradient(#d9d6cf,#6d7686)}
.coach h3{position:absolute;left:116px;top:18px;font-size:19px;font-weight:700;color:#333}
.coach .mail{position:absolute;left:116px;top:46px;font-size:12px;color:#888}
.coach p{position:absolute;left:14px;top:84px;right:14px;font-style:italic;font-size:14px;line-height:22px;color:#444}
.coach p a{color:var(--accent);text-decoration:none}

/* footer */
.footer{top:3216px;height:253px;background:var(--footer);color:#ddd}
.f-col{width:220px}
.f-col h4{font-family:'Raleway',sans-serif;font-weight:400;font-size:17px;letter-spacing:1px;text-transform:uppercase;color:#eee;padding-bottom:10px;border-bottom:1px solid #666}
.f-col ul{list-style:none;margin-top:16px}
.f-col li{font-size:15px;line-height:33px;color:#ccc}
.f-col li::before{content:"›";margin-right:14px;color:#aaa}
.contact{font-size:13px;line-height:18px;color:#ddd;margin-top:18px}
.contact .row{display:flex;gap:10px;margin-bottom:14px}
.contact svg{flex:none;margin-top:2px}
.page-box{width:270px;height:166px;background:var(--white);margin-top:22px;padding:10px;color:#333;font-size:12px}
.page-box .mark{width:42px;height:42px;background:var(--navy);float:left;margin-right:10px}
.page-box .name{font-weight:700;color:var(--navy);font-size:13px}
.page-box .count{clear:both;padding-top:6px;font-size:11px}
.fans{display:flex;gap:8px;margin-top:6px}
.fans div{width:42px;text-align:center;font-size:10px}
.fans i{display:block;width:42px;height:42px;background:linear-gradient(#bbb,#666);margin-bottom:2px}
.copyright{top:3469px;height:47px;background:var(--footer-bottom);color:#bbb;font-size:13px;display:flex;align-items:center;justify-content:center}
</style>
</head>
<body>

<header class="topbar">
  <div class="abs brand"><span class="brand-mark"></span>HARBOR KITE</div>
  <div class="abs phone">
    <svg width="26" height="26" viewBox="0 0 26 26"><circle cx="13" cy="13" r="13" fill="#fff"/><path d="M9 7l3 3-1.6 1.8c.8 1.8 2 3 3.8 3.8L16 14l3 3-1.8 2C11.5 19 7 14.5 7 8.8z" fill="#2f5a80"/></svg>
    123-456-7890
  </div>
</header>

<section class="hero">
  <div class="abs" style="inset:0" role="img" aria-label="Silhouette of a person with raised arms on a mountain top against a golden sky"></div>
  <h1 class="abs hero-title">Step by step<br>to a richer life</h1>
  <div class="abs btn-start">GET STARTED</div>
  <div class="abs video">
    <div class="video-stage" role="img" aria-label="Video still of the two coaches standing together"></div>
    <div class="video-play"><svg width="62" height="62" viewBox="0 0 62 62"><path d="M25 19l19 12-19 12z" fill="#555"/></svg></div>
    <div class="video-bar">
      <svg width="464" height="47" viewBox="0 0 464 47">
        <path d="M12 17l11 7-11 7z" fill="#ddd"/>
        <path d="M34 20h5l6-5v18l-6-5h-5z" fill="#ddd"/>
        <rect x="58" y="21" width="170" height="6" rx="3" fill="#3d8fd1"/>
        <rect x="228" y="21" width="220" height="6" rx="3" fill="#111"/>
      </svg>
    </div>
  </div>
</section>

<section class="about">
  <h2 class="abs sec-title" style="top:42px">About <span>Harbor Kite</span></h2>
  <div class="abs divider" style="top:98px"></div>
  <p class="abs lede" style="top:140px">Lorem ipsum dolor sit amet, consectetur adipiscing elit. Vestibulum gravida ipsum nec tempor aliquam. Quisque sit amet est vel purus imperdiet ullamcorper lobortis id magna. Nulla in tellus risus. Morbi vitae tortor tincidunt velit aliquam sodales. Vivamus ex erat, pulvinar nec nunc vitae, maximus aliquet nunc. Aenean cursus dui et enim mattis, a blandit arcu volutpat. Donec leo turpis, viverra at justo ut, placerat ultricies nibh.</p>
  <div class="abs btn-small" style="left:546px;top:253px;width:108px">Read More</div>
</section>

<section class="why">
  <h2 class="abs sec-title" style="top:33px">Why <span>choose us</span></h2>
  <div class="abs divider" style="top:89px"></div>
  <p class="abs lede" style="top:138px">Lorem ipsum dolor sit amet, consectetuer adipiscing elit, sed diam nonummy nibh euismod tincidunt ut laoreetfgf dolore magna aliquam erat volutpat. tincidunt ut laoreetfgf dolore magna aliquam erat volutpat Lorem ipsum dolor sit amet.</p>
  <div class="abs portrait" role="img" aria-label="Portrait of a smiling coach in a dark suit"></div>
</section>

<section class="life">
  <svg class="abs life-lines" viewBox="0 0 320 260">
    <g stroke="#5e86aa" stroke-width="2" fill="none">
      <line x1="48" y1="42" x2="160" y2="178"/><line x1="272" y1="42" x2="160" y2="178"/>
      <line x1="48" y1="218" x2="160" y2="178"/><line x1="272" y1="218" x2="160" y2="178"/>
    </g>
    <circle cx="160" cy="178" r="24" fill="#4c76a0"/>
  </svg>
  <div class="abs life-item left" style="left:145px;top:74px"><h3>Rat race lifestyle</h3><p>Lorem ipsum dolor sit amet, consectetuer adipiscing el Lorem ipsum dolor sit amet, consectetuer adipiscing el..</p></div>
  <div class="abs life-icon" style="left:462px;top:66px;background:#2a9fd8" role="img" aria-label="Running businessman icon"></div>
  <div class="abs life-icon" style="left:676px;top:66px;background:#f0b323" role="img" aria-label="Relaxed person icon"></div>
  <div class="abs life-item" style="left:757px;top:74px"><h3>A richer lifestyle</h3><p>Lorem ipsum dolor sit amet, consectetuer adipiscing el Lorem ipsum dolor sit amet, consectetuer adipiscing el..</p></div>
  <div class="abs life-item left" style="left:145px;top:252px"><h3>Prosperous lifestyle</h3><p>Lorem ipsum dolor sit amet, consectetuer adipiscing el Lorem ipsum dolor sit amet, consectetuer adipiscing el..</p></div>
  <div class="abs life-icon" style="left:462px;top:244px;background:#8c7a66" role="img" aria-label="Award rosette icon"></div>
  <div class="abs life-icon" style="left:676px;top:244px;background:#46b04a" role="img" aria-label="Cheering person icon"></div>
  <div class="abs life-item" style="left:757px;top:252px"><h3>Freedom lifestyle</h3><p>Lorem ipsum dolor sit amet, consectetuer adipiscing el Lorem ipsum dolor sit amet, consectetuer adipiscing el..</p></div>
</section>
<svg class="abs life-pointer" viewBox="0 0 70 35"><path d="M0 0h70L35 35z" fill="#2f5a80"/></svg>

<section class="products">
  <h2 class="abs sec-title" style="top:42px">Our <span>products</span></h2>
  <div class="abs divider" style="top:98px"></div>
  <div class="abs col-rule" style="left:449px;top:170px;height:280px"></div>
  <div class="abs col-rule" style="left:743px;top:170px;height:280px"></div>
  <div class="abs product" style="left:182px;top:184px">
    <h3>Engångsession</h3>
    <div class="medal" style="background:radial-gradient(circle at 40% 35%,#e7a26a,#b8662f 60%,#7e3f17)" role="img" aria-label="Bronze medal"></div>
    <div class="price">Pris 650 SEK</div>
    <div class="includes">Inkluderar 1 session</div>
    <div class="btn-small">Boka Tid</div>
  </div>
  <div class="abs product" style="left:470px;top:184px">
    <h3>Silverpaketet</h3>
    <div class="medal" style="background:radial-gradient(circle at 40% 35%,#fafafa,#c4c4c4 60%,#8a8a8a)" role="img" aria-label="Silver medal"></div>
    <div class="price">Pris 3050 SEK</div>
    <div class="includes">Inkluderar 5 sessioner</div>
    <div class="btn-small">Boka Tid</div>
  </div>
  <div class="abs product" style="left:758px;top:184px">
    <h3>Guldpaketet</h3>
    <div class="medal" style="background:radial-gradient(circle at 40% 35%,#fff07a,#f1c20f 60%,#b98a00)" role="img" aria-label="Gold medal"></div>
    <div class="price">Pris 5800 SEK</div>
    <div class="includes">Inkluderar 10 sessioner</div>
    <div class="btn-small">Boka Tid</div>
  </div>
</section>

<section class="testimonials">
  <h2 class="abs sec-title" style="top:42px">Clients <span>testimonials</span></h2>
  <div class="abs divider" style="top:98px"></div>
  <svg class="abs arrow" style="left:120px;top:196px" viewBox="0 0 20 40"><path d="M18 2L3 20l15 18" stroke="#888" stroke-width="2" fill="none"/></svg>
  <svg class="abs arrow" style="left:1054px;top:196px" viewBox="0 0 20 40"><path d="M2 2l15 18L2 38" stroke="#888" stroke-width="2" fill="none"/></svg>
  <div class="abs quote" style="left:176px;top:158px;height:200px">
    <p>Uppiggande och inspirerande! Kommer med enkla vardagstips såväl som svårare tips. Ett roligt sätt att få en spark i baken, så att ekonomi-energin bibehålls! Tack för ett bra samtal!</p>
    <div class="quote-rule" style="top:140px"></div>
    <cite style="top:170px">- Helena Brattvik</cite>
  </div>
  <div class="abs quote" style="left:633px;top:158px;height:200px">
    <p>Värdefullast för mig var kunskapen om alternativa investeringssställen som inte är börs eller eget ägande.</p>
    <div class="quote-rule" style="top:140px"></div>
    <cite style="top:170px">- Annika Sjöstedt</cite>
  </div>
</section>

<section class="team">
  <h2 class="abs sec-title" style="top:36px">Our <span>team</span></h2>
  <div class="abs divider" style="top:92px"></div>
  <div class="abs coach" style="left:178px;top:170px">
    <div class="coach-photo a" role="img" aria-label="Portrait of coach Joakim Hedlund"></div>
    <h3>Joakim Hedlund</h3>
    <div class="mail">joakim@harborkite.se</div>
    <p>Mångsidig investerare med fokus på alternativa och högriskinvesteringar Förutom börsen, investerar Joakim i onoterade startup-bolag och olika internetbaserade investeringar sådsom P2P-lending, onlinespel och appar.</p>
  </div>
  <div class="abs coach" style="left:614px;top:170px">
    <div class="coach-photo b" role="img" aria-label="Portrait of coach Mattias Rönnberg"></div>
    <h3>Mattias Rönnberg</h3>
    <div class="mail">mattias@harborkite.se</div>
    <p>Mattias har en bred bakgrund inom ekonomi och IT. Som investerare ligger hans fokus på utdelningsaktier, fastigheter och internetbaserat entreprenörskap. Han har också en lång erfarenhet och en stor passion...<a href="#">read more</a></p>
  </div>
</section>

<footer class="footer">
  <div class="abs f-col" style="left:173px;top:28px;width:176px">
    <h4>Quick links</h4>
    <ul><li>Blogg</li><li>Coaching</li><li>Om oss</li></ul>
  </div>
  <div class="abs f-col" style="left:443px;top:28px;width:228px">
    <h4>Contact details</h4>
    <div class="contact">
      <div class="row"><svg width="12" height="16" viewBox="0 0 12 16"><path d="M6 0a6 6 0 016 6c0 4-6 10-6 10S0 10 0 6a6 6 0 016-6z" fill="#eee"/><circle cx="6" cy="6" r="2.2" fill="#333"/></svg><div><b>Harbor Kite</b><br>Harbor Kite AB<br>Lyckevägen 12<br>412 60 Göteborg</div></div>
      <div class="row"><svg width="14" height="14" viewBox="0 0 26 26"><path d="M9 5l3.5 3.5-2 2.2c1 2.3 2.5 3.8 4.8 4.8l2.2-2 3.5 3.5-2.2 2.5C11 20 6 15 6 8z" fill="#eee"/></svg>123-456-7890</div>
      <div class="row"><svg width="14" height="11" viewBox="0 0 14 11"><rect width="14" height="11" fill="#eee"/><path d="M0 0l7 6 7-6" stroke="#333" fill="none"/></svg>team@harborkite.se</div>
    </div>
  </div>
  <div class="abs f-col" style="left:750px;top:28px;width:276px">
    <h4>Follow us online</h4>
    <div class="page-box">
      <div class="mark"></div>
      <div class="name">Harbor Kite</div>
      <div class="count">4,575,118 people follow Harbor Kite</div>
      <div class="fans">
        <div><i role="img" aria-label="Follower photo"></i>John</div>
        <div><i role="img" aria-label="Follower photo"></i>Nate</div>
        <div><i role="img" aria-label="Follower photo"></i>Rita</div>
        <div><i role="img" aria-label="Follower photo"></i>Wilson</div>
        <div><i role="img" aria-label="Follower photo"></i>Sarah</div>
      </div>
    </div>
  </div>
</footer>
<div class="abs copyright" style="left:0;width:1200px">Copyright © 2016 Harbor Kite. All Rights Reserved.</div>

</body>
</html>
```